Unique Business Card Design

Unique Business Card design for our orthotic and prosthetic company. Our logo is on our website, color is light blue. Unique shape (artificial leg shaped, vertical, etc..) preferred. Logo, business name, individual name and basic demographics needed.

Industry/Entity Type

Business

Contact Information for Business Card

Logo, Industry, Phone # Logo, "Prosthetic & Orthotic Services" Place to add individual name and contact info

Colors
cee9f5

Requirements
Must have
• The icon must be there, placement of "Prosthetic & Orthotic Services" can be moved
Nice to have
• Like the mix of light blue, and a little darker blue. One design included the icons from my website which was a nice touch

```html
<!DOCTYPE html>
<html lang="en">
<head>
<meta charset="utf-8">
<title>Stridewell Inc. Business Card</title>
<link rel="stylesheet" href="https://fonts.googleapis.com/css2?family=Open+Sans:wght@400;600;700&family=Cormorant+Garamond:ital,wght@1,500&display=swap">
<style>
  :root {
    --brand-blue: #1862b3;
    --brand-blue-dark: #0f4f98;
    --light-blue: #cee9f5;
    --ink: #4a4f55;
    --rule: #c9ccd0;
    --paper: #ffffff;
    --backdrop: #e7eaee;
  }
  * { box-sizing: border-box; margin: 0; padding: 0; }
  html, body {
    width: 1200px; height: 950px; overflow: hidden;
    background: var(--backdrop);
    font-family: "Open Sans", Arial, sans-serif;
  }
  .sheet {
    position: relative; width: 1200px; height: 950px;
    display: flex; flex-direction: column; align-items: center; justify-content: center; gap: 50px;
  }
  .card {
    position: relative; width: 700px; height: 400px;
    box-shadow: 0 6px 18px rgba(0,0,0,0.12);
    overflow: hidden;
  }

  /* Front */
  .card--front { background: var(--paper); }
  .front__brand { position: absolute; left: 52px; top: 52px; display: flex; align-items: center; gap: 18px; }
  .brand-dot { width: 72px; height: 72px; border-radius: 50%; background: var(--brand-blue); flex: none; }
  .brand-name {
    font-weight: 700; font-size: 27px; letter-spacing: 0.5px; color: var(--brand-blue); line-height: 1;
    padding-bottom: 6px; border-bottom: 2px solid var(--brand-blue);
  }
  .brand-tagline {
    font-family: "Cormorant Garamond", Georgia, serif; font-style: italic; font-weight: 500;
    font-size: 17px; color: var(--brand-blue); margin-top: 5px;
  }
  .front__divider { position: absolute; left: 470px; top: 50px; width: 1px; height: 300px; background: var(--rule); }
  .front__address {
    position: absolute; left: 500px; top: 150px;
    font-size: 16px; line-height: 1.65; color: var(--ink);
  }
  .front__person { position: absolute; left: 52px; top: 210px; }
  .person-name { font-size: 23px; font-weight: 600; color: var(--brand-blue); }
  .person-name .credentials { font-size: 15px; font-weight: 400; }
  .contact-list { list-style: none; margin-top: 12px; }
  .contact-list li {
    display: flex; align-items: center; gap: 10px;
    font-size: 15px; line-height: 1.65; color: var(--ink);
  }
  .contact-list svg { width: 15px; height: 15px; fill: var(--brand-blue); flex: none; }

  /* Back */
  .card--back { background: var(--brand-blue); color: var(--paper); }
  .back__dot { position: absolute; left: 90px; top: 115px; width: 120px; height: 120px; border-radius: 50%; background: var(--paper); }
  .back__brand { position: absolute; left: 250px; top: 140px; }
  .back__brand .brand-name { color: var(--paper); font-size: 40px; border-bottom: 3px solid var(--paper); padding-bottom: 8px; }
  .back__brand .brand-tagline { color: var(--paper); font-size: 24px; margin-top: 6px; }
  .back__web {
    position: absolute; left: 50px; bottom: 48px;
    font-size: 14px; font-style: italic; letter-spacing: 0.4px; color: var(--light-blue);
  }
  .back__rule { position: absolute; left: 250px; bottom: 56px; width: 400px; height: 1px; background: rgba(255,255,255,0.6); }
</style>
</head>
<body>
<main class="sheet">

  <section class="card card--front" aria-label="Business card front">
    <div class="front__brand">
      <span class="brand-dot"></span>
      <div>
        <div class="brand-name">STRIDEWELL INC.</div>
        <div class="brand-tagline">Prosthetic &amp; Orthotic Services</div>
      </div>
    </div>

    <div class="front__divider"></div>

    <address class="front__address" style="font-style:normal">
      820 Harbor Ave.<br>
      Brooklyn, NY 11200<br>
      www.stridewellinc.com
    </address>

    <div class="front__person">
      <div class="person-name">Miriam Castellane, <span class="credentials">CO LPO</span></div>
      <ul class="contact-list">
        <li>
          <svg viewBox="0 0 16 16" aria-hidden="true"><path d="M3 1h3l1.5 4-2 1.3a9 9 0 0 0 4.2 4.2L11 8.5l4 1.5v3a2 2 0 0 1-2 2A12 12 0 0 1 1 3a2 2 0 0 1 2-2z"/></svg>
          212.555.0140
        </li>
        <li>
          <svg viewBox="0 0 16 16" aria-hidden="true"><path d="M4 1h8v4H4zM1 6h14v7h-3v2H4v-2H1zm4 5v3h6v-3z"/></svg>
          212.555.0162
        </li>
        <li>
          <svg viewBox="0 0 16 16" aria-hidden="true"><path d="M4 0h8a1 1 0 0 1 1 1v14a1 1 0 0 1-1 1H4a1 1 0 0 1-1-1V1a1 1 0 0 1 1-1zm1 2v10h6V2zm3 11a1 1 0 1 0 0 2 1 1 0 0 0 0-2z"/></svg>
          917-555-0188
        </li>
        <li>
          <svg viewBox="0 0 16 16" aria-hidden="true"><path d="M1 3h14v10H1zm1.5 1.2L8 8.5l5.5-4.3z"/></svg>
          mcastellane@stridewellinc.com
        </li>
      </ul>
    </div>
  </section>

  <section class="card card--back" aria-label="Business card back">
    <span class="back__dot"></span>
    <div class="back__brand">
      <div class="brand-name">STRIDEWELL INC.</div>
      <div class="brand-tagline">Prosthetic &amp; Orthotic Services</div>
    </div>
    <div class="back__web">www.stridewellinc.com</div>
    <div class="back__rule"></div>
  </section>

</main>
</body>
</html>
```